vorne matcha

I'm a local business called 'VORNE' and will be sourcing organic ceremonial grade matcha tea through a private labeler in Japan. I need a sleek layout for the label that wraps around the tin that holds the 30g of matcha. I have samples of inspiration and designs that I like. This is very high end matcha so I would like for it to have an expensive look. I also have the dimensions of the label for the tin to show. I have specifics of things that need to be on the label, so please let me know if you need any of that information at this point!

Target Market(s)

High end matcha tea drinkers. The label files I sent are what my eye was drawn to.

Industry/Entity Type

matcha

Font styles to use
Other font styles liked:
• I like the font styles of the samples I uploaded in the photos

Colors

Designer to choose only greyscale colors for use in the design.

Requirements
Must have
• In the biggest lettering of them all in the center is MATCHA. (everything capitalized).Above it, my brand name which is VORNE. and if it looks good, Vorne no.7 like the Duvelle no.5.below the MATCHA, I would like it to say Ceremonial Grade.Another thing... Design wise!I would like the tin to be silver, and the label to be a sort of creme, in between white color with black lettering. Also, I would like the font to be more along the lines of the Ma Verte fonts I sent you... the files that show the cologne bottle with the silver top, creme label, and lettering:)Thanks so much and can't to see what you doOn it as well, the USDA certified organic label, which is in one of the screenshots I uploaded.There needs to be the net weight which is 30g. and also that it is sourced in Uji, Japanmy website on the back: www.saptamatcha.comThe nutrition facts and how to use I will send later:)
Nice to have
• my signature somewhere (like the coffee picture I sent)

```html
<!DOCTYPE html>
<html lang="en">
<head>
<meta charset="UTF-8">
<title>Vorne Matcha – Tin Labels</title>
<link rel="stylesheet" href="https://fonts.googleapis.com/css2?family=Montserrat:wght@400;500;600;700&display=swap">
<style>
  :root {
    --paper: #ffffff;
    --label: #fdfdfc;
    --ink: #141414;
    --ink-soft: #3a3a3a;
    --rule: #8c8c8c;
    --leaf-light: #f4f4f4;
    --leaf-mid: #ececec;
    --badge: #d9d9d9;
    --shadow: rgba(0, 0, 0, 0.16);
  }
  * { margin: 0; padding: 0; box-sizing: border-box; }
  html, body {
    width: 1200px; height: 1001px; overflow: hidden;
    background: var(--paper);
    font-family: "Montserrat", Arial, sans-serif;
    color: var(--ink);
  }
  .canvas { position: relative; width: 1200px; height: 1001px; }

  /* Lid label */
  .lid-label {
    position: absolute; left: 400px; top: 70px;
    width: 400px; height: 400px; border-radius: 50%;
    background: var(--label);
    box-shadow: 0 14px 34px var(--shadow);
    overflow: hidden;
    text-align: center;
  }
  .lid-label .brand {
    position: absolute; top: 128px; width: 100%;
    font-size: 20px; font-weight: 500; letter-spacing: 4px;
  }
  .lid-label .product {
    position: absolute; top: 163px; width: 100%;
    font-size: 56px; font-weight: 700; letter-spacing: 1.5px; line-height: 1;
  }
  .lid-label .divider {
    position: absolute; top: 238px; left: 120px; width: 160px;
    border-top: 1px solid var(--ink);
  }
  .lid-label .grade {
    position: absolute; top: 252px; width: 100%;
    font-size: 19px; font-weight: 400; letter-spacing: 2px;
  }
  .lid-label .weight {
    position: absolute; top: 305px; width: 100%;
    font-size: 17px; font-weight: 500; letter-spacing: 0.5px;
  }

  /* Wrap label */
  .wrap-label {
    position: absolute; left: 50px; top: 585px;
    width: 1100px; height: 237px;
    background: var(--label);
    box-shadow: 0 18px 30px var(--shadow);
    overflow: hidden;
  }
  .leaf-pattern {
    position: absolute; inset: 0;
    background: radial-gradient(circle at 30% 40%, var(--leaf-light), var(--label) 70%),
                linear-gradient(90deg, var(--leaf-mid), var(--label) 50%, var(--leaf-mid));
    opacity: 0.7;
  }

  .info-panel {
    position: absolute; left: 100px; top: 38px; width: 150px;
    text-align: center;
  }
  .signature {
    display: block; margin: 0 auto; width: 110px; height: 34px;
    background: linear-gradient(90deg, var(--leaf-mid), var(--badge), var(--leaf-mid));
    border-radius: 3px;
  }
  .info-panel .website {
    margin-top: 12px; font-size: 9px; color: var(--ink-soft);
  }
  .cert-row {
    margin-top: 8px; display: flex; justify-content: center; gap: 12px;
  }
  .cert-badge {
    width: 42px; height: 42px; border-radius: 50%;
    background: var(--badge);
  }
  .info-panel .origin {
    margin-top: 6px; font-size: 9px; color: var(--ink-soft);
  }
  .info-panel .net-weight {
    margin-top: 3px; font-size: 12px; font-weight: 500;
  }

  .center-mark {
    position: absolute; left: 377px; top: 58px; width: 257px;
    text-align: center;
  }
  .center-mark .brand {
    font-size: 16px; font-weight: 500; letter-spacing: 3px;
  }
  .center-mark .product {
    margin-top: 12px;
    font-size: 40px; font-weight: 700; letter-spacing: 1px; line-height: 1;
  }
  .center-mark .divider {
    width: 120px; margin: 14px auto 10px;
    border-top: 1px solid var(--ink);
  }
  .center-mark .grade {
    font-size: 15px; font-weight: 400; letter-spacing: 1.6px;
  }

  .detail-panel {
    position: absolute; left: 708px; top: 50px; width: 262px;
  }
  .detail-line {
    display: flex; align-items: flex-end; gap: 6px;
    font-size: 9px; font-weight: 500; letter-spacing: 0.3px;
    margin-bottom: 50px;
  }
  .detail-line .fill-rule {
    flex: 1; border-bottom: 1px solid var(--rule); margin-bottom: 3px;
  }
</style>
</head>
<body>
<main class="canvas">

  <section class="lid-label" aria-label="Lid label">
    <div class="brand">VORNE</div>
    <div class="product">MATCHA</div>
    <div class="divider"></div>
    <div class="grade">CEREMONIAL GRADE</div>
    <div class="weight">30G</div>
  </section>

  <section class="wrap-label" aria-label="Wrap-around tin label">
    <div class="leaf-pattern" role="img" aria-label="Scattered tea leaf line illustrations in light grey"></div>

    <div class="info-panel">
      <span class="signature" role="img" aria-label="Handwritten owner signature"></span>
      <p class="website">www.vornematcha.com</p>
      <div class="cert-row">
        <span class="cert-badge" role="img" aria-label="Organic certification badge"></span>
        <span class="cert-badge" role="img" aria-label="Japanese organic certification badge"></span>
      </div>
      <p class="origin">sourced in Uji, Japan</p>
      <p class="net-weight">NET WEIGHT: 30G</p>
    </div>

    <div class="center-mark">
      <div class="brand">VORNE</div>
      <div class="product">MATCHA</div>
      <div class="divider"></div>
      <div class="grade">CEREMONIAL GRADE</div>
    </div>

    <div class="detail-panel">
      <div class="detail-line"><span>INGREDIENTS:</span><span class="fill-rule"></span></div>
      <div class="detail-line"><span>HOW TO USE:</span><span class="fill-rule"></span></div>
    </div>
  </section>

</main>
</body>
</html>
```